Popup Nightclub Grand Opening Flyer

We need to design a flyer for the grand opening of an upscale, exclusive nightclub called "Lantern". The design needs to be chic and exclusive. The background should be black and the text should primarily be white. We like minimalist designs.

Here is the text for the flyer
-
Velvetroll Atlanta Presents

Lantern (LOGO)

A Popup Nightclub Experience
For one night Only

Friday, October 18, 2013
Party begins at 9PM

INVITE ONLY

See invitation for location details
(Velvetroll Atlanta logo)

-
Examples we like

http://cdn4-x.pressfolio-example.com/sites/default/files/styles/image_content_width/hash/3b/fd/2468013579_4421_flyer.jpg?itok=K9rtQw2z

http://files.hubspace-example.net/files/8Hqq-Tr72WWE3kaRbTmcxP5QZK2F396J8nbRw4CKMHfdX2Y7qSEF-MqjxDoNrLY3QCyQJD7npjGaRq3k-Mhx6hqf3MDSWf8r3/2zenSaturdays.jpg

http://morvex-example.com/wp-content/uploads/siteskin/widgetkit/gallery/2zen/2zen-gen_qstay4-01.jpg

Hi All, one thing that we are seeing that we don't like is on over emphasis on the phrase "a popup nightclub experience" please don't make this the largest thing on the flyer

Target Market(s)

Target market is 25-35 year olds who are affluent (rich) and like luxury brands

Requirements
Must have
• Dark Background
Nice to have
• Velvetroll Logo on the bottom
Modern text that isn't curvy
Should not have
• Curved text

```html
<!DOCTYPE html>
<html lang="en">
<head>
<meta charset="utf-8">
<title>Lantern Nightclub — A Popup Nightclub Experience</title>
<link rel="stylesheet" href="https://fonts.googleapis.com/css2?family=Arimo:wght@400;700&display=swap">
<style>
  :root {
    --ink: #000000;
    --pattern-mid: #1d1d1d;
    --pattern-edge: #050505;
    --white: #ffffff;
    --silver: #a6a6a6;
    --grey: #8f8f8f;
    --rule: #cfcfcf;
    --neon: #e9e51c;
    --neon-glow: rgba(233, 229, 28, 0.55);
    --mark-light: #d9d9d9;
    --mark-dark: #3a3a3a;
  }
  * { margin: 0; padding: 0; box-sizing: border-box; }
  html, body {
    width: 787px;
    height: 1200px;
    overflow: hidden;
    background: var(--ink);
  }
  .flyer {
    position: relative;
    width: 787px;
    height: 1200px;
    overflow: hidden;
    background: var(--ink);
    font-family: "Arimo", Arial, sans-serif;
    color: var(--white);
    text-align: center;
  }
  .backdrop {
    position: absolute;
    inset: 0;
    background: radial-gradient(ellipse 70% 55% at 50% 38%, var(--pattern-mid) 0%, #111 45%, var(--pattern-edge) 100%);
  }
  .line {
    position: absolute;
    left: 0;
    width: 100%;
    line-height: 1;
    text-transform: uppercase;
    white-space: nowrap;
  }
  .presenter {
    top: 47px;
    font-size: 26px;
    font-weight: 700;
    color: var(--silver);
  }
  .brand-mark {
    position: absolute;
    left: 50%;
    top: 130px;
    width: 400px;
    height: 400px;
    margin-left: -200px;
    border-radius: 50%;
    background: linear-gradient(120deg, var(--mark-light) 0%, #8a8a8a 45%, var(--mark-dark) 100%);
  }
  .brand-name {
    top: 668px;
    font-size: 54px;
    font-weight: 400;
    letter-spacing: 9px;
    color: var(--white);
  }
  .brand-sub {
    top: 731px;
    font-size: 32px;
    font-weight: 400;
    letter-spacing: 5px;
    color: var(--white);
  }
  .tagline {
    top: 810px;
    font-size: 34px;
    font-weight: 700;
    color: var(--white);
  }
  .tagline-rule {
    position: absolute;
    left: 100px;
    top: 854px;
    width: 587px;
    height: 2px;
    background: var(--rule);
  }
  .one-night {
    top: 865px;
    font-size: 53px;
    font-weight: 700;
    color: var(--neon);
    text-shadow: 0 0 14px var(--neon-glow), 0 0 4px var(--neon-glow);
  }
  .date {
    top: 944px;
    font-size: 28px;
    font-weight: 700;
    letter-spacing: 1.5px;
    color: var(--grey);
  }
  .access {
    top: 1002px;
    font-size: 28px;
    font-weight: 700;
    color: var(--white);
  }
  .access-note {
    top: 1047px;
    font-size: 13px;
    font-weight: 700;
    color: var(--white);
  }
  .host {
    position: absolute;
    left: 0;
    top: 1118px;
    width: 100%;
    display: flex;
    justify-content: center;
    align-items: center;
    gap: 14px;
  }
  .host-dot {
    width: 36px;
    height: 36px;
    border-radius: 50%;
    background: var(--white);
  }
  .host-name {
    font-size: 28px;
    font-weight: 400;
    letter-spacing: 1px;
    line-height: 1;
    color: var(--white);
    text-transform: uppercase;
  }
</style>
</head>
<body>
  <main class="flyer">
    <div class="backdrop" role="img" aria-label="Black background with a subtle dark damask pattern"></div>

    <p class="line presenter">Velvetroll Atlanta Presents</p>

    <div class="brand-mark" aria-hidden="true"></div>
    <h1 class="line brand-name">Lantern</h1>
    <p class="line brand-sub">Nightclub</p>

    <h2 class="line tagline">A Popup Nightclub Experience</h2>
    <div class="tagline-rule"></div>
    <p class="line one-night">For One Night Only</p>
    <p class="line date">Friday October 18 2013 @ 9:00PM</p>
    <p class="line access">Invite Only</p>
    <p class="line access-note">See invitation for location details</p>

    <div class="host">
      <span class="host-dot" aria-hidden="true"></span>
      <span class="host-name">Velvetroll Atlanta</span>
    </div>
  </main>
</body>
</html>
```